Construction company that specializes in roofing and siding

https://maplecrestbuild.example/featured-projects/

https://www.bramwickhomesllc.example/#

https://www.tallgrovecontractors.example/residential-siding-services/

Please model a website after these examples
I posted a doc that has some content to get you started. I will upload more content and photos as the site progresses.

Coded - Design and coding required

5+ page

```html
<!DOCTYPE html>
<html lang="en">
<head>
<meta charset="utf-8">
<title>Hearthline Construction — Roofing &amp; Siding in Minnesota</title>
<link href="https://fonts.googleapis.com/css2?family=Lato:wght@400;700;900&family=Syncopate:wght@700&display=swap" rel="stylesheet">
<style>
:root{
  --teal:#12d3d8;
  --ink:#111111;
  --dark:#161616;
  --gray-bar:#6a6a6c;
  --foot-bar:#4f4f52;
  --text:#333333;
  --white:#ffffff;
}
*{box-sizing:border-box;margin:0;padding:0}
html,body{width:1200px;height:3656px;overflow:hidden;background:var(--white)}
body{font-family:"Lato",sans-serif;color:var(--text)}
.page{position:relative;width:1200px;height:3656px;overflow:hidden}
.abs{position:absolute}
.display{font-family:"Syncopate",sans-serif;font-weight:700;text-transform:uppercase;color:var(--ink);letter-spacing:1px;white-space:nowrap}
.btn{position:absolute;background:var(--teal);color:var(--white);font-weight:700;font-size:16px;display:flex;align-items:center;justify-content:center}

/* top bar */
.topbar{left:0;top:0;width:1200px;height:31px;background:var(--gray-bar);color:var(--white);font-size:13px}
.topbar span{position:absolute;top:8px;display:flex;align-items:center;gap:6px;white-space:nowrap}
.topbar svg{width:12px;height:12px}

/* brand */
.brand{position:absolute;display:flex;align-items:center;gap:12px}
.brand-name{font-family:"Lato",sans-serif;font-weight:900;letter-spacing:2px;line-height:1}
.brand-head{left:112px;top:53px}
.brand-head .brand-mark{width:54px;height:54px;background:#3b3b3d}
.brand-head .brand-name{font-size:25px;color:#3b3b3d}
.brand-head .brand-sub{font-size:12px;letter-spacing:4px;color:#3b3b3d;font-weight:700;margin-top:4px}
.brand-foot{left:112px;top:3060px}
.brand-foot .brand-mark{width:82px;height:82px;background:var(--white)}
.brand-foot .brand-name{font-size:30px;color:var(--white)}
.brand-foot .brand-sub{font-size:14px;letter-spacing:5px;color:var(--white);font-weight:700;margin-top:4px}

/* header */
.header{left:0;top:31px;width:1200px;height:115px;background:var(--white)}
.nav a{position:absolute;top:47px;font-size:15px;color:#333;text-decoration:none;white-space:nowrap}
.nav a.drop::after{content:"";display:inline-block;width:5px;height:5px;border-right:1px solid #555;border-bottom:1px solid #555;transform:rotate(45deg);margin-left:4px;position:relative;top:-3px}

/* hero */
.hero{left:0;top:146px;width:1200px;height:627px;background:linear-gradient(180deg,#5d5e60 0%,#8b8c8c 40%,#6f7070 75%,#8e8f8d 100%)}
.hero-title{left:0;width:1200px;text-align:center;color:var(--white)}
.hero-sub{top:476px;left:0;width:1200px;text-align:center;color:var(--white);font-size:25px;font-weight:700}
.hero-edge{left:0;top:680px;width:1200px;height:95px}

/* promise */
.promise-title{top:856px;left:0;width:1200px;text-align:center;font-size:31px}
.promise-text{top:917px;left:200px;width:800px;text-align:center;font-size:20.5px;line-height:29px;color:#333}
.promise-text .sig{color:var(--teal);font-weight:700}

/* about */
.about{left:0;top:1111px;width:1200px;height:492px}
.about-title{top:1230px;left:656px;font-size:31px;color:var(--white)}
.about-text{top:1290px;left:654px;width:490px;font-size:15.5px;line-height:22.5px;color:var(--white)}

/* services */
.services-title{top:1641px;left:0;width:1200px;text-align:center;font-size:31px}
.card{position:absolute;top:1721px;width:234px;height:195px;overflow:hidden}
.card .label{position:absolute;left:0;bottom:16px;width:100%;text-align:center;font-family:"Syncopate",sans-serif;font-weight:700;font-size:19px;color:var(--white);letter-spacing:1px;text-transform:uppercase;white-space:nowrap}
.card.active{background:#4b4c4e}
.card.active .label{top:40px;bottom:auto}

/* contact */
.contact{left:0;top:2002px;width:1200px;height:396px;background:linear-gradient(180deg,#5a6168 0%,#6d7377 50%,#5f6a5a 100%);clip-path:polygon(0 0,100% 0,100% 100%,0 93%)}
.contact-title{top:2080px;left:0;width:1200px;text-align:center;font-size:31px;color:var(--white)}
.contact-sub{top:2132px;left:0;width:1200px;text-align:center;font-size:15.5px;font-weight:700;color:var(--white)}
.field-label{top:2176px;font-size:13.5px;color:var(--white)}
.field{top:2204px;width:205px;height:42px;border:1px solid #dcdcdc;background:rgba(255,255,255,.08)}

/* gallery */
.gallery-title{top:2426px;left:0;width:1200px;text-align:center;font-size:31px}
.tile{position:absolute}

/* footer */
.footer{left:0;top:3008px;width:1200px;height:591px;background:var(--dark);color:var(--white)}
.vrule{left:448px;top:3072px;width:1px;height:64px;background:#555}
.news-title{left:475px;top:3068px;font-size:21px;font-weight:700;color:var(--white)}
.news-sub{left:475px;top:3099px;font-size:12px;font-weight:700;line-height:17px;color:var(--white)}
.news-input{left:715px;top:3082px;width:239px;height:44px;border:1px solid #ccc;border-radius:3px;font-size:12.5px;color:var(--white);padding:14px 18px}
.hrule{left:112px;top:3197px;width:978px;height:1px;background:#3a3a3a}
.col-title{top:3264px;font-size:20px;font-weight:700;color:var(--white)}
.col-bar{top:3300px;width:88px;height:2px;background:var(--teal)}
.col-bar::after{content:"";position:absolute;right:-2px;top:-2px;width:6px;height:6px;border-radius:50%;background:var(--teal)}
.col-text{left:112px;top:3326px;width:220px;font-size:15px;line-height:22.5px;color:var(--white)}
.links{list-style:none}
.links li{position:absolute;font-size:15px;color:var(--white);white-space:nowrap}
.links li::before{content:"";display:inline-block;width:6px;height:6px;border-right:1.5px solid #fff;border-top:1.5px solid #fff;transform:rotate(45deg);margin-right:16px;position:relative;top:-2px}
.social{position:absolute;top:3455px;width:21px;height:21px;border-radius:2px}
.post-thumb{position:absolute;left:858px;width:69px;height:65px;background:linear-gradient(135deg,#8c8f93,#b7b2aa)}
.post-title{position:absolute;left:938px;width:160px;font-size:15px;font-weight:700;line-height:21px;color:var(--white)}
.post-date{position:absolute;left:940px;font-size:12.5px;color:var(--white);display:flex;align-items:center;gap:6px}
.post-date i{display:inline-block;width:8px;height:8px;background:var(--teal)}
.copy{left:0;top:3599px;width:1200px;height:57px;background:var(--foot-bar);color:var(--white);font-size:13px;text-align:center;line-height:57px}
</style>
</head>
<body>
<div class="page">

  <!-- top bar -->
  <div class="abs topbar">
    <span style="left:112px">
      <svg viewBox="0 0 12 12"><circle cx="6" cy="6" r="5" fill="none" stroke="#fff" stroke-width="1.4"/><path d="M6 3v3l2 1" stroke="#fff" stroke-width="1.2" fill="none"/></svg>
      Monday - Saturday : <b>8 Am - 5:30 PM</b>&nbsp;&nbsp;&nbsp; Sunday : <b>Closed</b>
    </span>
    <span style="left:727px">
      <svg viewBox="0 0 12 12"><path d="M2 1l2.5 0 1 3-1.5 1a6 6 0 0 0 3 3l1-1.5 3 1V11C5 11 1 7 1 2z" fill="#fff"/></svg>
      + 1 555 010 0199
    </span>
    <span style="left:866px">
      <svg viewBox="0 0 12 12"><rect x="1" y="2.5" width="10" height="7" fill="none" stroke="#fff" stroke-width="1.2"/><path d="M1 3l5 3.5L11 3" stroke="#fff" stroke-width="1.2" fill="none"/></svg>
      info@hearthline.example
    </span>
  </div>

  <!-- header -->
  <header class="abs header">
    <nav class="nav">
      <a style="left:425px">Home</a>
      <a class="drop" style="left:502px">Roofing</a>
      <a class="drop" style="left:590px">Siding</a>
      <a class="drop" style="left:667px">Gutters</a>
      <a class="drop" style="left:755px">Windows</a>
      <a class="drop" style="left:855px">Repair</a>
      <a class="drop" style="left:935px">Storm damage repair</a>
    </nav>
  </header>
  <div class="brand brand-head">
    <div class="brand-mark"></div>
    <div><div class="brand-name">HEARTHLINE</div><div class="brand-sub">CONSTRUCTION</div></div>
  </div>

  <!-- hero -->
  <section class="abs hero" role="img" aria-label="Covered back porch with wicker armchairs and a ceiling fan"></section>
  <div class="abs hero-title display" style="top:310px;font-size:46px;color:#fff">Hearthline</div>
  <div class="abs hero-title display" style="top:385px;font-size:62px;color:#fff;letter-spacing:0">Construction</div>
  <div class="abs hero-sub">is your source for roofing and siding in Minnesota.</div>
  <div class="btn" style="left:523px;top:539px;width:155px;height:41px">Contact Us</div>
  <svg class="abs hero-edge" viewBox="0 0 1200 95" preserveAspectRatio="none">
    <polygon points="0,0 600,68 1200,0 1200,95 0,95" fill="#fff"/>
    <polygon points="110,20 600,68 1120,16 600,93" fill="#12d3d8"/>
  </svg>

  <!-- promise -->
  <h2 class="abs display promise-title">The Hearthline Promise</h2>
  <p class="abs promise-text">
    You deserve timely service, high quality materials, expert installation, and an ironclad warranty. That is what we promise to deliver. I invite you to put us to the test today.<br>
    Sincerely,<br>
    <span class="sig">Dale Brenner, Owner</span><br>
    Hearthline Construction
  </p>

  <!-- about -->
  <svg class="abs about" viewBox="0 0 1200 492">
    <polygon points="0,0 597,71 597,425 0,460" fill="#6a6a6a" role="img" aria-label="Roofer in work gloves nailing asphalt shingles"/>
    <polygon points="597,71 1200,0 1200,492 0,492 0,460 597,425" fill="#111"/>
  </svg>
  <h2 class="abs display about-title">About Us</h2>
  <p class="abs about-text">In 2016 Dale Brenner started helping people with their home improvement projects. HIs very first job was installing window trim for a wonderful homeowner in Forest lake MN. He did his best work and made sure he treated his first customer like family. Afterall, his first customer was Marla Brenner, his Mom.</p>
  <div class="btn" style="left:654px;top:1440px;width:155px;height:41px">Read More</div>

  <!-- services -->
  <h2 class="abs display services-title">What We Do</h2>
  <div class="card" style="left:-139px;background:linear-gradient(135deg,#9aa6b0,#c7b37a)" role="img" aria-label="Technician repairing an outdoor AC unit"><div class="label">Repair</div></div>
  <div class="card" style="left:112px;background:linear-gradient(135deg,#7f8a6f,#a39a8c)" role="img" aria-label="Roofer using a nail gun on shingles"><div class="label">Roofing</div></div>
  <div class="card active" style="left:359px" role="img" aria-label="Worker installing siding"><div class="label">Siding</div>
    <div class="btn" style="left:40px;top:95px;width:155px;height:41px">Read More</div></div>
  <div class="card" style="left:606px;background:linear-gradient(135deg,#c9cdd1,#8d9298)" role="img" aria-label="Worker fitting gutters under the eaves"><div class="label">Gutters</div></div>
  <div class="card" style="left:854px;background:linear-gradient(135deg,#9ca59a,#d0d2cc)" role="img" aria-label="Installer fitting a window frame"><div class="label">Windows</div></div>
  <div class="card" style="left:1102px;background:linear-gradient(135deg,#6d7563,#a5a89b)" role="img" aria-label="Crew clearing storm debris from a house"><div class="label" style="text-align:left;padding-left:62px">Storm</div></div>

  <!-- contact -->
  <section class="abs contact" role="img" aria-label="Gray two-storey house with a lawn at dusk"></section>
  <h2 class="abs display contact-title">Contact Us</h2>
  <p class="abs contact-sub">Hearthline Construction is your source for roofing and siding in Minnesota.</p>
  <span class="abs field-label" style="left:191px">Name</span>
  <span class="abs field-label" style="left:415px">Phone</span>
  <span class="abs field-label" style="left:638px">Email</span>
  <div class="abs field" style="left:189px"></div>
  <div class="abs field" style="left:413px"></div>
  <div class="abs field" style="left:636px"></div>
  <div class="btn" style="left:856px;top:2204px;width:154px;height:42px">Submit</div>

  <!-- gallery -->
  <h2 class="abs display gallery-title">Gallery</h2>
  <div class="tile" style="left:128px;top:2502px;width:227px;height:181px;background:linear-gradient(135deg,#5f8a3a,#9bb86a)" role="img" aria-label="Crew clearing a fallen tree by a house"></div>
  <div class="tile" style="left:128px;top:2699px;width:227px;height:226px;background:linear-gradient(135deg,#7fa7a0,#cfd6c8)" role="img" aria-label="Worker installing a glass window"></div>
  <div class="tile" style="left:367px;top:2502px;width:228px;height:247px;background:linear-gradient(135deg,#8e9aa6,#d2d6da)" role="img" aria-label="Man cleaning a roof gutter"></div>
  <div class="tile" style="left:367px;top:2760px;width:228px;height:165px;background:linear-gradient(135deg,#c9ccd0,#8b9a7a)" role="img" aria-label="Painter on a ladder beside a white house"></div>
  <div class="tile" style="left:606px;top:2502px;width:227px;height:159px;background:linear-gradient(135deg,#b7bcc2,#8a7f74)" role="img" aria-label="Roofers laying shingles"></div>
  <div class="tile" style="left:606px;top:2673px;width:227px;height:252px;background:linear-gradient(180deg,#8fb0cc,#3e4a4e 55%,#5c8a3c)" role="img" aria-label="Dark gray sided house with a green lawn"></div>
  <div class="tile" style="left:846px;top:2502px;width:227px;height:247px;background:linear-gradient(135deg,#aebbc6,#6e5b52)" role="img" aria-label="Roofers working on a shingle roof"></div>
  <div class="tile" style="left:846px;top:2760px;width:227px;height:165px;background:linear-gradient(135deg,#c4c7ca,#8f5f3b)" role="img" aria-label="Technician servicing an air conditioning unit"></div>

  <!-- footer -->
  <footer class="abs footer"></footer>
  <div class="brand brand-foot">
    <div class="brand-mark"></div>
    <div><div class="brand-name">HEARTHLINE</div><div class="brand-sub">CONSTRUCTION</div></div>
  </div>
  <div class="abs vrule"></div>
  <div class="abs news-title">News Subscription</div>
  <div class="abs news-sub">Get Latest Deals from Hearthline's<br>Inbox &amp; Subscribe Now</div>
  <div class="abs news-input">Email Address
    <svg class="abs" style="right:16px;top:16px" width="13" height="11" viewBox="0 0 13 11"><rect x="1" y="1" width="11" height="9" fill="none" stroke="#12d3d8" stroke-width="1.3"/><path d="M1 1.5l5.5 4 5.5-4" fill="none" stroke="#12d3d8" stroke-width="1.3"/></svg>
  </div>
  <div class="btn" style="left:966px;top:3082px;width:124px;height:44px">Subscribe</div>
  <div class="abs hrule"></div>

  <div class="abs col-title" style="left:112px">About Company</div>
  <div class="abs col-bar" style="left:112px"></div>
  <p class="abs col-text">We are helping a lot more people now, but we haven't lost the dedication to service and craftsmanship that I had on my very first job.”</p>
  <span class="social" style="left:112px;background:#1877f2"></span>
  <span class="social" style="left:139px;background:#fff"></span>
  <span class="social" style="left:166px;background:#e60023"></span>
  <span class="social" style="left:193px;background:#c13584"></span>
  <span class="social" style="left:220px;background:#ff0000"></span>

  <div class="abs col-title" style="left:396px">Quick Links</div>
  <div class="abs col-bar" style="left:396px"></div>
  <ul class="links">
    <li style="left:396px;top:3326px">Home</li>
    <li style="left:396px;top:3362px">About Us</li>
    <li style="left:396px;top:3398px">What we do</li>
    <li style="left:396px;top:3434px">Gallery</li>
    <li style="left:396px;top:3470px">Contact Us</li>
  </ul>

  <div class="abs col-title" style="left:613px">What we do</div>
  <div class="abs col-bar" style="left:613px"></div>
  <ul class="links">
    <li style="left:613px;top:3326px">Roofing</li>
    <li style="left:613px;top:3362px">Siding</li>
    <li style="left:613px;top:3398px">Gutters</li>
    <li style="left:613px;top:3434px">Windows</li>
    <li style="left:613px;top:3470px">Repair</li>
    <li style="left:613px;top:3506px">Storm damage repair</li>
  </ul>

  <div class="abs col-title" style="left:858px">Recent Posts</div>
  <div class="abs col-bar" style="left:858px"></div>
  <div class="post-thumb" style="top:3329px" role="img" aria-label="Red brick house"></div>
  <div class="post-title" style="top:3326px">Lorem ipsum dolor sit amet, consectetur</div>
  <div class="post-date" style="top:3374px"><i></i>June 27 2024</div>
  <div class="post-thumb" style="top:3420px" role="img" aria-label="Roofer at work"></div>
  <div class="post-title" style="top:3416px">Lorem ipsum dolor sit amet, consectetur</div>
  <div class="post-date" style="top:3464px"><i></i>June 27 2024</div>

  <div class="abs copy">Copyright © 2024 Hearthline Construction. All rights reserved.</div>
</div>
</body>
</html>
```